MEDICAL CLINIC LETTERHEAD

Design is a letterhead for a non-profit medical center. The name of the clinic is VITARIDGE Community Health Center. Although the full name must be included, the community health center part is more of a description and should be less visible - i attached an example of what I mean by that (ATTACHED IMAGE IS AN EXAMPLE OF FONT SIZES NOT A DESIGN IDEA). Please design something modern, cool looking and unique because I can always download free templates.
Phone, email, website and etc will be added later.

Industry/Entity Type

MEDICAL

```html
<!DOCTYPE html>
<html lang="en">
<head>
<meta charset="utf-8">
<title>VITARIDGE Community Health Center – Letterhead</title>
<link rel="stylesheet" href="https://fonts.googleapis.com/css2?family=Lato:wght@400;700&family=Mulish:wght@500&family=Allura&display=swap">
<style>
  :root{
    --navy:#1b2a4a;
    --gold:#a98f54;
    --ink:#3b3b3b;
    --contact-ink:#1f1f1f;
    --backdrop:#e3e3e3;
  }
  *{margin:0;padding:0;box-sizing:border-box;}
  html,body{width:1153px;height:1200px;overflow:hidden;background:var(--backdrop);}
  .letterhead{
    position:absolute;left:169px;top:30px;width:815px;height:1140px;
    background:radial-gradient(ellipse at 50% 35%, #ffffff 0%, #f6f6f6 60%, #f1f0f0 100%);
    box-shadow:0 6px 24px rgba(0,0,0,.18);
    overflow:hidden;
    font-family:"Lato",sans-serif;color:var(--ink);
  }
  .brand-name{
    position:absolute;left:62px;top:88px;
    font-family:"Lato",sans-serif;font-weight:700;font-size:42px;letter-spacing:1px;
    color:var(--navy);
  }
  .contact{
    position:absolute;left:557px;top:47px;height:92px;
    border-left:1.5px solid var(--gold);padding-left:12px;
    font-family:"Mulish",sans-serif;font-weight:500;color:var(--contact-ink);
  }
  .contact-org{font-size:14px;line-height:18px;margin-top:-1px;}
  .contact-list{list-style:none;margin-top:6px;}
  .contact-list li{display:flex;align-items:center;font-size:14px;line-height:19.5px;}
  .contact-list svg{width:13px;height:13px;margin-right:11px;fill:var(--gold);}
  .letter{position:absolute;left:63px;top:257px;width:690px;font-size:14.3px;line-height:17.5px;}
  .date{font-size:16px;}
  .recipient{margin-top:19px;font-size:15px;line-height:18.5px;}
  .company{margin-top:18px;font-size:15px;line-height:18.5px;}
  .salutation{margin-top:20px;font-size:19.5px;font-weight:700;}
  .body p{text-align:justify;margin-top:17px;}
  .body p:first-child{margin-top:18px;}
  .closing{margin-top:38px;font-size:15px;}
  .signature{margin-top:14px;font-family:"Allura",cursive;font-size:44px;color:#2a2a2a;line-height:1;}
  .footer-band{
    position:absolute;left:0;bottom:0;width:815px;height:140px;
    background:linear-gradient(to bottom, rgba(27,42,74,0) 0%, var(--navy) 35%, var(--gold) 70%, var(--gold) 100%);
  }
</style>
</head>
<body>
  <main class="letterhead">
    <div class="brand-name">VITARIDGE</div>

    <aside class="contact">
      <div class="contact-org">VITARIDGE Community<br>Health Center</div>
      <ul class="contact-list">
        <li><svg viewBox="0 0 16 16" aria-hidden="true"><path d="M1 5c0-2 3-3 7-3s7 1 7 3v1h-4V5H5v1H1zM4 7h8l2 6H2z"/></svg>555-014-2637</li>
        <li><svg viewBox="0 0 16 16" aria-hidden="true"><path d="M1 4h14v9H1z M1 4l7 5 7-5" stroke="#fff" stroke-width="1"/></svg>info@example-mail.com</li>
        <li><svg viewBox="0 0 16 16" aria-hidden="true"><circle cx="8" cy="8" r="7"/></svg>www.example-web.com</li>
      </ul>
    </aside>

    <article class="letter">
      <div class="date">Feb-03-2022</div>
      <div class="recipient">Mr, Alan Reyes<br>President</div>
      <div class="company">Northfield Corporation<br>123 Street Name, Suite# 10<br>City, State, 120023</div>
      <div class="salutation">Dear Mr, Alan</div>
      <div class="body">
        <p>Lorem ipsum dolor sit amet, consectetur adipisicing elit, sed do eiusmod tempor incididunt ut labore et dolore magna aliqua. Ut enim ad minim veniam, quis nostrud exercitation ullamco laboris nisi ut aliquip ex ea commodo consequat. Duis aute irure dolor in reprehenderit in voluptate velit esse cillum dolore eu fugiat nulla pariatur.</p>
        <p>Lorem ipsum dolor sit amet, consectetur adipisicing elit, sed do eiusmod tempor incididunt ut labore et dolore magna aliqua. Ut enim ad minim veniam, quis nostrud exercitation ullamco laboris nisi ut aliquip ex ea commodo consequat. Duis aute irure dolor in reprehenderit in voluptate velit esse cillum dolore eu fugiat nulla pariatur.</p>
        <p>Lorem ipsum dolor sit amet, consectetur adipisicing elit, sed do eiusmod tempor incididunt ut labore et dolore magna aliqua. Ut enim ad minim veniam, quis nostrud exercitation ullamco laboris nisi ut aliquip ex ea commodo consequat.</p>
        <p>Excepteur sint occaecat cupidatat non proident, sunt in culpa qui officia deserunt mollit anim id est laborum. re et dolore magnam aliquam quaerat voluptatem.</p>
      </div>
      <div class="closing">Regards</div>
      <div class="signature">Daniel Brooks</div>
    </article>

    <div class="footer-band" role="img" aria-label="Decorative footer band in navy and gold"></div>
  </main>
</body>
</html>
```